KAJU Freightways #ALLKAJU Business Cards & Letterhead

I am looking to business cards designed for our organization. We are currently undergoing a small re-branding that is taking place. Our organization is called KAJU Freightways and we are headquartered in Phoenix, AZ. We primarily provide transportation and logistics services to the Marlow Parcel Bureau who is our largest customer. I would like to see a design that incorporates name, title, contact info, website, and address (this will be different depending on the employee). I would also like to see some color on the business card using our logo colors or a variation. I would like our logo on the back of the business card with the website displayed. The final design should communicate that we are a next generation transportation operate that focuses on being driver-first, customer-centric, innovative, and sustainable.We would also like our #ALLKAJU catch phrase incorporated as well.

Target Market(s)

Transportation & Logistics

Industry/Entity Type

Trucking Company

Contact Information for Business Card

-First and Last Name
-Position Title
-Contact Phone
-Contact Email
-Physical Address

Font styles to use
Serif

Colors

Designer to choose colors to be used in the design.

Requirements
Must have
• -KAJU logo prominently displayed
• -#ALLKAJU catch phrase used
• -Some amount of color, design gradient, etc.
• -Logo on the back with website listed (https://www.kajufreightco.example)

```html
<!DOCTYPE html>
<html lang="en">
<head>
<meta charset="utf-8">
<title>KAJU Freightways Business Card</title>
<link href="https://fonts.googleapis.com/css2?family=Roboto:wght@300;400;500;700&display=swap" rel="stylesheet">
<style>
  :root {
    --backdrop: #c9c9c9;
    --paper: #ffffff;
    --ink: #0a3a48;
    --teal: #053745;
    --teal-soft: #0a4250;
    --green: #7cc242;
    --white: #ffffff;
  }
  * { margin: 0; padding: 0; box-sizing: border-box; }
  html, body {
    width: 1125px; height: 1200px; overflow: hidden;
    background: var(--backdrop);
    font-family: "Roboto", Arial, sans-serif;
  }
  .canvas { position: relative; width: 1125px; height: 1200px; }
  .card {
    position: absolute; left: 150px; width: 825px; height: 470px;
    border-radius: 24px; overflow: hidden;
  }
  .card--front { top: 98px; background: var(--paper); }
  .card--back { top: 631px; background: var(--teal); }

  .wordmark {
    position: absolute; font-weight: 700; line-height: 1;
    transform: translate(-50%, -50%); white-space: nowrap;
  }
  .card--front .wordmark { left: 269px; top: 235px; font-size: 58px; color: var(--ink); }
  .divider {
    position: absolute; left: 413px; top: 124px; width: 2px; height: 222px;
    background: var(--ink);
  }
  .details { position: absolute; left: 453px; top: 128px; color: var(--ink); font-weight: 300; }
  .details__name { font-size: 27px; font-weight: 500; color: var(--green); line-height: 30px; }
  .details__title { font-size: 20px; line-height: 28px; }
  .details__address { margin-top: 12px; font-size: 20px; line-height: 25px; }
  .contact { margin-top: 14px; list-style: none; }
  .contact li { display: flex; align-items: center; font-size: 20px; line-height: 25.5px; }
  .contact svg { width: 16px; height: 16px; margin-right: 13px; flex: none; }
  .contact .accent { color: var(--green); }

  .world-area {
    position: absolute; left: 10px; top: 10px; width: 805px; height: 440px;
    background: radial-gradient(ellipse at 55% 45%, var(--teal-soft) 0%, var(--teal) 70%);
  }
  .card--back .wordmark { left: 412px; top: 220px; font-size: 92px; color: var(--white); }
  .back-footer {
    position: absolute; left: 0; right: 0; top: 372px; text-align: center;
    color: var(--white); font-weight: 300; font-size: 19px; line-height: 26px;
  }
  .back-footer__tag { color: var(--green); font-weight: 500; letter-spacing: 1px; }
</style>
</head>
<body>
<div class="canvas">
  <section class="card card--front">
    <div class="wordmark">KAJU</div>
    <div class="divider"></div>
    <div class="details">
      <p class="details__name">Dana Whitfield</p>
      <p class="details__title">Manager</p>
      <p class="details__address">4410 North Canyon Ridge Road<br>Phoenix, AZ 85016</p>
      <ul class="contact">
        <li>
          <svg viewBox="0 0 16 16" aria-hidden="true"><path fill="#7cc242" d="M3.2 1.2l2.4-.4 1.6 3.6-1.6 1.2c.8 1.8 2 3 3.8 3.8l1.2-1.6 3.6 1.6-.4 2.4c-.2.8-1 1.4-1.8 1.4C6.4 13.2 2.8 9.6 1.8 3c0-.8.6-1.6 1.4-1.8z"/></svg>
          602-555-0148
        </li>
        <li>
          <svg viewBox="0 0 16 16" aria-hidden="true"><rect x="1" y="3" width="14" height="10" fill="#7cc242"/><path d="M1 3l7 6 7-6" stroke="#fff" stroke-width="1.4" fill="none"/></svg>
          info@kajufreightco.example
        </li>
        <li>
          <svg viewBox="0 0 16 16" aria-hidden="true"><circle cx="8" cy="8" r="7" fill="#7cc242"/><path d="M1 8h14M8 1c-3 3.5-3 10.5 0 14M8 1c3 3.5 3 10.5 0 14" stroke="#fff" stroke-width="1" fill="none"/></svg>
          <span>www.<span class="accent">kajufreightco</span>.example</span>
        </li>
      </ul>
    </div>
  </section>

  <section class="card card--back">
    <div class="world-area" role="img" aria-label="Faint dotted world map spread across the card"></div>
    <div class="wordmark">KAJU</div>
    <div class="back-footer">
      <p class="back-footer__tag">#ALLKAJU</p>
      <p>www.kajufreightco.example</p>
    </div>
  </section>
</div>
</body>
</html>
```